Construction Company

Design a clutter free business card, it can be double-sided utilizing the logo for VKM Ltd simple with all relevant contact information.

Please also a letterhead design to function for the purposes of invoicing, all mail requirements, with header to be distinctive while the footer ties page together and incorporates all necessary information.

For now, please use generic / dummy text and when a winner is selected, I will disclose the contact information.

Hi Designers! Please read the updated brief which includes the design of a business card and letterhead. Thank you!

```html
<!DOCTYPE html>
<html lang="en">
<head>
<meta charset="utf-8">
<title>VKM Ltd — Business Card</title>
<link rel="stylesheet" href="https://fonts.googleapis.com/css2?family=Arimo:wght@400&family=Tinos:wght@400;700&display=swap">
<style>
  :root {
    --canvas: #1b1b1d;
    --card: #0c0c0d;
    --brand-blue: #0a3bb5;
    --gold: #d2a21c;
    --text-light: #c9c9c9;
    --divider: #3a3a3a;
  }
  * { margin: 0; padding: 0; box-sizing: border-box; }
  html, body {
    width: 1200px; height: 900px; overflow: hidden;
    background: var(--canvas);
  }
  .sheet {
    width: 1200px; height: 900px;
    display: flex; align-items: center; justify-content: center; gap: 44px;
  }
  .card {
    width: 532px; height: 304px;
    background: var(--card);
    position: relative;
    box-shadow: 0 10px 30px rgba(0,0,0,.55);
  }
  .brand-name {
    font-family: "Tinos", serif;
    font-weight: 400;
    color: var(--brand-blue);
    display: flex; align-items: center; gap: 10px;
    letter-spacing: 1px;
    white-space: nowrap;
  }
  .brand-dot {
    width: 20px; height: 20px; border-radius: 50%;
    background: var(--gold);
    flex: none;
  }
  /* Front: logo + contact */
  .card-front .brand-name {
    position: absolute; left: 36px; top: 150px;
    font-size: 40px;
  }
  .card-front .divider {
    position: absolute; left: 262px; top: 46px; bottom: 46px;
    width: 1px; background: var(--divider);
  }
  .contact {
    position: absolute; left: 290px; top: 56px; right: 16px;
    font-family: "Arimo", sans-serif; color: var(--text-light);
  }
  .contact-name {
    font-family: "Tinos", serif; font-weight: 700;
    color: var(--gold); font-size: 17px; letter-spacing: .5px;
    text-transform: uppercase;
  }
  .contact-title { font-size: 14px; margin-top: 2px; }
  .contact-list { list-style: none; margin-top: 16px; font-size: 14px; line-height: 20px; }
  .contact-list li { display: flex; align-items: center; gap: 8px; white-space: nowrap; }
  .contact-list svg { width: 13px; height: 13px; flex: none; }
  .address { margin-top: 16px; font-size: 14px; line-height: 18px; padding-left: 21px; white-space: nowrap; }
  /* Back: logo centred */
  .card-back .brand-name {
    position: absolute; left: 0; right: 0; top: 118px;
    justify-content: center;
    font-size: 52px;
  }
</style>
</head>
<body>
<main class="sheet">
  <section class="card card-front" aria-label="Business card front">
    <div class="brand-name"><span class="brand-dot"></span>VKM Ltd</div>
    <div class="divider"></div>
    <div class="contact">
      <p class="contact-name">Marcus Hale</p>
      <p class="contact-title">Managing Director</p>
      <ul class="contact-list">
        <li>
          <svg viewBox="0 0 16 16" aria-hidden="true"><path fill="var(--gold)" d="M3.5 1.5l2.5 3-1.5 1.8c.9 1.9 2.3 3.3 4.2 4.2L10.5 9l3 2.5-1.2 2.3c-.3.5-.9.8-1.5.7C5.9 13.6 2.4 10.1 1.5 5.2c-.1-.6.2-1.2.7-1.5z"/></svg>
          020 7946 0321
        </li>
        <li>
          <svg viewBox="0 0 16 16" aria-hidden="true"><rect x="4" y="1" width="8" height="14" rx="1.5" fill="none" stroke="var(--gold)" stroke-width="1.6"/><circle cx="8" cy="12.3" r=".9" fill="var(--gold)"/></svg>
          077 0090 0458
        </li>
        <li>
          <svg viewBox="0 0 16 16" aria-hidden="true"><rect x="1" y="3.5" width="14" height="9" fill="var(--gold)"/><path d="M1 3.5l7 5 7-5" fill="none" stroke="var(--card)" stroke-width="1.2"/></svg>
          hello@vkmbuild.co
        </li>
        <li>
          <svg viewBox="0 0 16 16" aria-hidden="true"><g fill="none" stroke="var(--gold)" stroke-width="1.3"><circle cx="8" cy="8" r="6.3"/><ellipse cx="8" cy="8" rx="2.8" ry="6.3"/><path d="M1.7 8h12.6M2.7 4.8h10.6M2.7 11.2h10.6"/></g></svg>
          www.vkmbuild.co
        </li>
      </ul>
      <p class="address">18 Harbour Lane, Eastfield<br>EF4 2RT, United Kingdom</p>
    </div>
  </section>

  <section class="card card-back" aria-label="Business card back">
    <div class="brand-name"><span class="brand-dot"></span>VKM Ltd</div>
  </section>
</main>
</body>
</html>
```